Automotive component supplier needs a business card design

We need a business card design for our company called Velran Global Components Ltd based in the UK. We are a supplier of interior and exterior components to premium car manufacturers such as Corvel Ashby, Hadley Fenn, Marquist and Tavarelli. We would like to see a modern business card design that uses the colour blue.

Target Market(s)

Premium automotive car manufacturers.

Industry/Entity Type

Automotive

Contact Information for Business Card

Company Name : Velran Global Components Limited
Address: 17 Marlow Yard, Upper Heath, Warwick, CV31 8QL, United Kingdom
Web Address : www.velrancomponents-example.co.uk

Font styles to use
Other font styles liked:
• Helvetica

Colors
3176b5
0255a3
85acd3
cfdeed
cee9f5
85cae6
34a6d7
0692cd
9bcb3c

Requirements
Must have
• Clear company logo and a mixture of blue colours.
Nice to have
• A high quality modern image.
Should not have
• Multiple colours.

```html
<!DOCTYPE html>
<html lang="en">
<head>
<meta charset="utf-8">
<title>Velran Global Components – Business Card</title>
<link href="https://fonts.googleapis.com/css2?family=Arimo:wght@400;700&display=swap" rel="stylesheet">
<style>
  :root {
    --backdrop: #2a2b2d;
    --brand-blue: #0692cd;
    --deep-blue: #0a82c0;
    --faint-blue: #34a6d7;
    --lime: #9bcb3c;
    --white: #ffffff;
  }
  * { margin: 0; padding: 0; box-sizing: border-box; }
  html, body {
    width: 1200px; height: 900px; overflow: hidden;
    background: var(--backdrop);
    font-family: "Arimo", sans-serif;
  }
  .canvas { position: relative; width: 1200px; height: 900px; }

  .card {
    position: absolute;
    width: 620px; height: 354px;
    overflow: hidden;
  }

  /* Card back */
  .card-back { left: 110px; top: 90px; background: var(--brand-blue); }
  .card-back .pattern-area {
    position: absolute; inset: 0;
    background: linear-gradient(135deg, var(--brand-blue), var(--deep-blue));
  }
  .card-back .wordmark {
    position: absolute; right: 40px; bottom: 120px;
    display: flex; align-items: center; gap: 8px;
    color: var(--white); font-weight: 700; font-size: 40px; letter-spacing: 1px;
  }
  .card-back .wordmark .dot {
    width: 12px; height: 12px; background: var(--white);
  }
  .card-back .descriptor {
    position: absolute; right: 40px; bottom: 100px;
    color: var(--white); font-size: 11px; letter-spacing: 2.5px;
  }

  /* Card front */
  .card-front { left: 470px; top: 456px; background: var(--white); }
  .card-front .split { position: absolute; inset: 0; }
  .card-front .front-wordmark {
    position: absolute; left: 40px; top: 152px;
    color: var(--brand-blue); font-weight: 700; font-size: 42px; letter-spacing: 1px;
  }
  .card-front .details {
    position: absolute; right: 30px; top: 36px;
    text-align: right; color: var(--white);
  }
  .holder-name { font-weight: 700; font-size: 18px; letter-spacing: 2px; }
  .holder-role { color: var(--lime); font-size: 13px; margin-top: 2px; }
  .address { font-size: 12px; line-height: 1.35; margin-top: 16px; }
  .contact-list { list-style: none; margin-top: 12px; font-size: 12px; line-height: 1.5; }
  .contact-list li { display: flex; justify-content: flex-end; align-items: center; gap: 7px; }
  .contact-list svg { width: 10px; height: 10px; flex: none; }
</style>
</head>
<body>
<main class="canvas">

  <section class="card card-back" aria-label="Business card back">
    <div class="pattern-area" role="img" aria-label="Faint repeating brand-mark pattern in light blue"></div>
    <div class="wordmark"><span class="dot"></span>VELRAN</div>
    <div class="descriptor">GLOBAL COMPONENTS</div>
  </section>

  <section class="card card-front" aria-label="Business card front">
    <svg class="split" viewBox="0 0 620 354" preserveAspectRatio="none" aria-hidden="true">
      <path d="M212 0 Q332 170 254 354 L620 354 L620 0 Z" fill="var(--lime)"/>
      <path d="M228 0 Q348 170 268 354 L620 354 L620 0 Z" fill="var(--brand-blue)" stroke="var(--white)" stroke-width="3"/>
    </svg>

    <div class="front-wordmark">VELRAN</div>

    <div class="details">
      <div class="holder-name">DORIAN HASKETT</div>
      <div class="holder-role">Director</div>
      <div class="address">17 Marlow Yard, Upper Heath<br>Warwick, CV31 8QL, UK</div>
      <ul class="contact-list">
        <li>780 555-0142
          <svg viewBox="0 0 12 12"><path d="M2 1h3l1 3-1.5 1a6 6 0 0 0 2.5 2.5L8 6l3 1v3a1 1 0 0 1-1 1C5 11 1 7 1 2a1 1 0 0 1 1-1z" fill="var(--lime)"/></svg>
        </li>
        <li>780 555-0187
          <svg viewBox="0 0 12 12"><rect x="3" y="0.5" width="6" height="11" rx="1" fill="none" stroke="var(--lime)" stroke-width="1.2"/><circle cx="6" cy="9.5" r="0.8" fill="var(--lime)"/></svg>
        </li>
        <li>hello@velran-example.co.uk
          <svg viewBox="0 0 12 12"><rect x="0.5" y="2" width="11" height="8" fill="var(--lime)"/><path d="M0.5 2l5.5 4.5L11.5 2" fill="none" stroke="var(--brand-blue)" stroke-width="1"/></svg>
        </li>
        <li>www.velrancomponents-example.co.uk
          <svg viewBox="0 0 12 12"><circle cx="6" cy="6" r="5" fill="none" stroke="var(--lime)" stroke-width="1.2"/><ellipse cx="6" cy="6" rx="2" ry="5" fill="none" stroke="var(--lime)" stroke-width="1"/><path d="M1 6h10" stroke="var(--lime)" stroke-width="1"/></svg>
        </li>
      </ul>
    </div>
  </section>

</main>
</body>
</html>
```